Brackwell Exteriors Needs a New Website!

We are an exteriors company specializing in vinyl siding, Corwin Maddox siding, aluminum soffit/fascia, trough. We do new construction work as well as renovations. We also build detached garages.
You can view our current website at www.brackwellfabricators.ca
I want to completely overhaul the website.
Our services are different now as we no longer do new home construction as well as we do not do the snow clearing.
I want to focus on 2 things in particular on the website:

1/ Exterior renovations

2/ Detached Garage construction.

I have included our logo in the attached files to use as well.

Some features we would like:

1/ Be able to easily attach a video from Clipverse/Reelio to highlight a product or service
2/ Quick chat or contact button that we can talk to a potential client quickly
3/ Meet the Team page that is interesting and fresh
4/ Place for us to put in helpful exterior tips/suggestions for homeowners.

Content is not important, but looking for the best design that will attract people once they click on our page and want to renovate with us.

Target Market(s)

People looking for renovations on their home, people looking to build a detached garage.

Industry/Entity Type

Residential Construction

Number of Pages Required

5+ page

Font styles to use
Sans Serif

Requirements
Must have
• Fresh and exciting home page.

Simple design. Don't want it over complicated or too much information to confuse the potential client.

Easy way to contact us.

Meet the team page that instills confidence
Nice to have
• Colour of website to go off our logo. Doesn't need to be an exact match, but something that goes well with our blue and grey.

```html
<!DOCTYPE html>
<html lang="en">
<head>
<meta charset="utf-8">
<title>Brackwell Exteriors</title>
<link href="https://fonts.googleapis.com/css2?family=Poppins:wght@400;500;600;700&family=Open+Sans:wght@400;600&display=swap" rel="stylesheet">
<style>
:root{
  --blue:#1159b0;
  --blue-dark:#0c4a96;
  --navy:#0f2540;
  --grey:#e6e6e6;
  --pale:#e3ebf3;
  --text:#444;
  --muted:#666;
  --white:#fff;
}
*{box-sizing:border-box;margin:0;padding:0}
html,body{width:1200px;height:4535px;overflow:hidden}
body{font-family:"Open Sans",sans-serif;color:var(--text);background:var(--white);position:relative}
h1,h2,h3,h4,.nav,.btn{font-family:"Poppins",sans-serif}
section,header,footer{position:relative;width:1200px;overflow:hidden}

/* header */
.site-header{height:111px}
.brand{position:absolute;left:144px;top:24px;display:flex;align-items:center;gap:14px}
.brand-dot{width:56px;height:56px;border-radius:50%;background:var(--blue)}
.brand-name{font-family:"Poppins",sans-serif;font-weight:600;font-size:30px;color:var(--blue);letter-spacing:.5px}
.search{position:absolute;left:677px;top:18px;width:216px;height:37px;background:#eee;border:1px solid #ccc;font-size:12px;color:#888;padding:10px 14px}
.search svg{position:absolute;right:12px;top:11px}
.quote-btn{position:absolute;left:910px;top:18px;width:146px;height:37px;background:var(--blue);color:#fff;font-size:12px;display:flex;align-items:center;justify-content:center;font-family:"Poppins",sans-serif}
.nav{position:absolute;right:144px;top:72px;display:flex;gap:32px;font-size:12px;color:#555;text-transform:uppercase}
.nav .active{color:var(--blue);border-bottom:1px solid var(--blue)}

/* hero */
.hero{height:584px}
.hero-photo{position:absolute;inset:0;background:linear-gradient(180deg,#6f8aa0 0%,#50606c 35%,#6a5548 60%,#3f5534 100%)}
.hero-title{position:absolute;top:330px;width:100%;text-align:center;color:#fff;font-weight:700;font-size:44px;text-shadow:0 2px 6px rgba(0,0,0,.4)}
.hero-arrow{position:absolute;top:342px;width:40px;height:40px;border-radius:50%;background:#fff}
.hero-arrow.prev{left:56px}.hero-arrow.next{left:1103px}
.hero-wedge{position:absolute;bottom:0;left:0}

/* intro */
.intro{height:372px;text-align:center}
.intro h2{position:absolute;top:70px;left:140px;width:920px;font-weight:500;font-size:33px;line-height:48px;color:var(--blue)}
.intro p{position:absolute;top:176px;left:144px;width:912px;font-size:14px;line-height:29px;color:var(--text)}

/* services */
.services{height:570px;background:var(--grey)}
.section-title{position:absolute;width:100%;text-align:center;font-weight:500;font-size:32px;color:var(--blue)}
.services .section-title{top:72px}
.service-card{position:absolute;top:130px;width:218px;height:264px;background:#fff;text-align:center;padding-top:28px}
.service-card h3{font-weight:400;font-size:15px;color:var(--blue);margin-top:14px}
.service-card p{font-size:10px;line-height:17px;color:var(--muted);width:190px;margin:10px auto 0}
.btn-outline{display:inline-block;margin-top:10px;border:1px solid #999;font-size:10px;padding:7px 10px;color:#555;font-family:"Poppins",sans-serif}
.services-wedge{position:absolute;bottom:0;left:0}

/* team */
.team{height:602px}
.team .section-title{top:66px}
.member{position:absolute;top:132px;width:300px;text-align:center}
.member-photo{height:334px;background:linear-gradient(160deg,#cfcac4,#9c8f84)}
.member h4{font-weight:500;font-size:16px;color:#222;margin-top:16px}
.member p{font-size:12px;color:#555;margin-top:6px;font-family:"Poppins",sans-serif}

/* work */
.work{height:598px}
.work-tile{position:absolute;width:298px;height:297px}
.work-feature{position:absolute;left:301px;top:300px;width:598px;height:297px;background:var(--blue);color:#fff;text-align:center;padding-top:72px}
.work-feature h3{font-weight:400;font-size:32px}
.work-feature p{font-size:11px;line-height:18px;width:290px;margin:10px auto 0}
.btn-white{display:inline-block;margin-top:14px;background:#fff;color:var(--blue);font-size:10px;padding:9px 18px;font-family:"Poppins",sans-serif}

/* tips */
.tips{height:537px}
.tips .section-title{top:73px}
.faq{position:absolute;left:144px;width:912px;background:var(--pale)}
.faq-head{height:46px;display:flex;align-items:center;padding:0 22px;font-family:"Poppins",sans-serif;font-size:16px;color:var(--blue);gap:10px}
.faq-head .chev{margin-left:auto}
.faq-body{border-top:1px solid #cfd9e4;padding:12px 22px 14px 48px;font-size:10px;line-height:18px;color:var(--muted);position:relative}
.faq-body svg{position:absolute;left:22px;top:15px}

/* video */
.video{height:519px}
.video-photo{position:absolute;inset:0;background:linear-gradient(180deg,#2c4f7c 0%,#264a74 45%,#3a3e4a 100%)}
.video-tint{position:absolute;inset:0;background:rgba(17,89,176,.35)}
.play{position:absolute;left:576px;top:206px}
.video h3{position:absolute;top:272px;width:100%;text-align:center;color:#fff;font-weight:500;font-size:31px}

/* contact */
.contact{height:401px}
.contact .section-title{top:80px}
.field{position:absolute;top:137px;width:218px;height:39px;border:1px solid #bbb;font-size:11px;color:#777;padding:12px 14px}
.field svg{position:absolute;right:14px;top:16px}
.message{position:absolute;left:144px;top:194px;width:912px;height:118px;border:1px solid #bbb;font-size:11px;color:#777;padding:12px 14px}
.submit{position:absolute;left:552px;top:333px;width:96px;height:35px;background:var(--blue);color:#fff;font-size:12px;display:flex;align-items:center;justify-content:center}

/* footer */
.site-footer{height:241px}
.footer-shape{position:absolute;top:0;left:0}
.footer-links{position:absolute;left:144px;top:158px;font-size:11px;color:#9fb3cc;font-family:"Poppins",sans-serif}
.footer-links span{margin:0 8px;color:#6e84a0}
.copyright{position:absolute;left:144px;top:188px;font-size:11px;color:#9fb3cc}
.social{position:absolute;left:943px;top:158px;display:flex;gap:28px}
.social i{display:block;width:18px;height:18px;border-radius:50%;background:#8aa0bb}
.live-chat{position:absolute;left:1091px;top:30px;width:68px;height:52px;background:var(--blue);border-radius:8px;color:#fff;font-size:12px;line-height:14px;text-align:center;padding-top:11px;font-family:"Poppins",sans-serif}
.live-chat::after{content:"";position:absolute;left:22px;bottom:-10px;border:7px solid transparent;border-top-color:var(--blue);border-left-color:var(--blue)}
</style>
</head>
<body>

<header class="site-header">
  <div class="brand"><span class="brand-dot"></span><span class="brand-name">Brackwell Exteriors</span></div>
  <div class="search">Search
    <svg width="14" height="14" viewBox="0 0 14 14"><circle cx="6" cy="6" r="4.5" fill="none" stroke="#1159b0" stroke-width="2"/><line x1="9.5" y1="9.5" x2="13" y2="13" stroke="#1159b0" stroke-width="2"/></svg>
  </div>
  <div class="quote-btn">REQUEST A QUOTE</div>
  <nav class="nav"><span class="active">Home</span><span>Our Services</span><span>Our Works</span><span>About Us</span><span>Team</span><span>Contact Us</span></nav>
</header>

<section class="hero">
  <div class="hero-photo" role="img" aria-label="Two-storey home with grey shingle siding lit warmly at dusk, patio and lawn in front"></div>
  <span class="hero-arrow prev"><svg width="40" height="40" viewBox="0 0 40 40"><path d="M23 12 L15 20 L23 28" fill="none" stroke="#1159b0" stroke-width="4"/></svg></span>
  <span class="hero-arrow next"><svg width="40" height="40" viewBox="0 0 40 40"><path d="M17 12 L25 20 L17 28" fill="none" stroke="#1159b0" stroke-width="4"/></svg></span>
  <h1 class="hero-title">EXPERIENCE THE BRACKWELL DIFFERENCE</h1>
  <svg class="hero-wedge" width="1200" height="90" viewBox="0 0 1200 90"><polygon points="0,90 1200,90 1200,80 700,76" fill="#fff"/><polygon points="0,6 700,76 0,80" fill="#1159b0"/><polygon points="0,80 700,76 1200,80 0,90" fill="#fff"/></svg>
</section>

<section class="intro">
  <h2>Honest and reliable construction servtice in Edmonton and area. We take pride in each and every project</h2>
  <p>Quisque aliquet ex nec est vestibulum pulvinar. Pellentesque convallis molestie enim sit amet efficitur. Etiam id imperdiet lectus. Vivamus lacus justo, ultrices nec erat in, euismod iaculis mauris. Vivamus eleifend vitae nulla vel malesuada. In ac malesuada lacus, et consectetur ante. Fusce vitae lectus sit amet mi pulvinar maximus. Aenean placerat, nibh vel accumsan aliquet, magna nibh accumsan nibh, ac tempus nunc ipsum ac tellus. Cras augue magna, placerat eget nulla non, congue suscipit neque.</p>
</section>

<section class="services">
  <h2 class="section-title">Services</h2>
  <div class="service-card" style="left:144px">
    <svg width="64" height="56" viewBox="0 0 64 56" fill="none" stroke="#333" stroke-width="2"><path d="M4 26 L32 4 L60 26"/><rect x="10" y="22" width="44" height="32"/><rect x="26" y="36" width="12" height="18"/><rect x="14" y="30" width="8" height="8"/><rect x="42" y="30" width="8" height="8"/></svg>
    <h3>New Home Exteriors</h3>
    <p>Etiam mattis augue vehicula odio posuere, sit amet tempus lectus luctus. Nulla facilisi.</p>
    <span class="btn-outline">READ MORE</span>
  </div>
  <div class="service-card" style="left:375px">
    <svg width="64" height="56" viewBox="0 0 64 56" fill="none" stroke="#333" stroke-width="2"><path d="M4 20 L32 4 L60 20 V54 H4 Z"/><rect x="14" y="24" width="36" height="30"/><rect x="20" y="36" width="24" height="12" rx="3"/><circle cx="25" cy="50" r="2"/><circle cx="39" cy="50" r="2"/></svg>
    <h3>Detached Garages</h3>
    <p>Etiam mattis augue vehicula odio posuere, sit amet tempus lectus luctus. Nulla facilisi.</p>
    <span class="btn-outline">READ MORE</span>
  </div>
  <div class="service-card" style="left:607px">
    <svg width="64" height="56" viewBox="0 0 64 56" fill="none" stroke="#333" stroke-width="2"><rect x="10" y="18" width="30" height="36"/><line x1="10" y1="30" x2="40" y2="30"/><line x1="10" y1="42" x2="40" y2="42"/><line x1="48" y1="4" x2="48" y2="54"/><line x1="20" y1="6" x2="60" y2="6"/><line x1="56" y1="6" x2="56" y2="18"/></svg>
    <h3>Exterior Renovations</h3>
    <p>Etiam mattis augue vehicula odio posuere, sit amet tempus lectus luctus. Nulla facilisi.</p>
    <span class="btn-outline">READ MORE</span>
  </div>
  <div class="service-card" style="left:838px">
    <svg width="64" height="56" viewBox="0 0 64 56" fill="none" stroke="#333" stroke-width="2"><path d="M8 54 V26 L32 4 L56 26 V54 Z"/><path d="M14 54 L32 30 L50 54"/><line x1="8" y1="40" x2="56" y2="40"/><line x1="32" y1="4" x2="32" y2="54"/></svg>
    <h3>Vinyl Siding</h3>
    <p>Etiam mattis augue vehicula odio posuere, sit amet tempus lectus luctus. Nulla facilisi.</p>
    <span class="btn-outline">READ MORE</span>
  </div>
  <svg class="services-wedge" width="1200" height="90" viewBox="0 0 1200 90"><polygon points="0,90 600,40 1200,40 1200,90" fill="#fff"/><polygon points="600,40 1200,0 1200,40" fill="#1159b0"/><polygon points="0,90 600,40 1200,40 1200,90" fill="#fff"/></svg>
</section>

<section class="team">
  <h2 class="section-title">Team</h2>
  <div class="member" style="left:144px"><div class="member-photo" role="img" aria-label="Portrait of William, team member, against a grey wall"></div><h4>William</h4><p>Nulla porttitor nibh ut mi feugiat</p></div>
  <div class="member" style="left:451px"><div class="member-photo" role="img" aria-label="Portrait of Madison, team member, against a grey wall"></div><h4>Madison</h4><p>Aliquam dignissim elit nec mauris</p></div>
  <div class="member" style="left:757px"><div class="member-photo" role="img" aria-label="Portrait of Alexander, team member, against a grey wall"></div><h4>Alexander</h4><p>Pellentesque vehicula nulla molestie</p></div>
</section>

<section class="work">
  <div class="work-tile" style="left:0;top:0;background:linear-gradient(180deg,#6d8a4a,#b9b4a4)" role="img" aria-label="Cream house with porch and flower garden"></div>
  <div class="work-tile" style="left:301px;top:0;background:linear-gradient(180deg,#50624a,#8a6a58)" role="img" aria-label="House with lit entrance and paved driveway"></div>
  <div class="work-tile" style="left:602px;top:0;background:linear-gradient(180deg,#8fb0d4,#2e3034)" role="img" aria-label="Dark roof and siding against a blue sky"></div>
  <div class="work-tile" style="left:902px;top:0;background:linear-gradient(180deg,#7c6a58,#3f6b34)" role="img" aria-label="Brick house with shrubs and front steps"></div>
  <div class="work-tile" style="left:0;top:300px;background:linear-gradient(180deg,#d8dadc,#8f8a82)" role="img" aria-label="White siding wall with patio chairs on a deck"></div>
  <div class="work-feature">
    <h3>Our Work</h3>
    <p>Aenean facilisis tincidunt lectus, id dictum nisi luctus eget. Vivamus efficitur ex condimentum, malesuada eros eget, feugiat nibh mattis augue.</p>
    <span class="btn-white">READ MORE</span>
  </div>
  <div class="work-tile" style="left:902px;top:300px;background:linear-gradient(180deg,#c9d2dc,#2f3338)" role="img" aria-label="Roofer working on a metal roof beside a brick chimney"></div>
</section>

<section class="tips">
  <h2 class="section-title">Helpful exterior tips/suggestions for homeowners</h2>
  <div class="faq" style="top:136px">
    <div class="faq-head"><svg width="14" height="14" viewBox="0 0 14 14"><circle cx="7" cy="7" r="7" fill="#1159b0"/><text x="7" y="11" font-size="10" text-anchor="middle" fill="#fff" font-family="sans-serif" font-weight="700">?</text></svg>Etiam vel massa elementum, bibendum tellus venenatis?<svg class="chev" width="12" height="8" viewBox="0 0 12 8"><path d="M1 7 L6 2 L11 7" fill="none" stroke="#1159b0" stroke-width="2"/></svg></div>
    <div class="faq-body"><svg width="14" height="14" viewBox="0 0 14 14"><circle cx="7" cy="7" r="7" fill="#999"/><rect x="6" y="6" width="2" height="5" fill="#fff"/><rect x="6" y="3" width="2" height="2" fill="#fff"/></svg>Pellentesque convallis molestie enim sit amet efficitur. Etiam id imperdiet lectus. Vivamus lacus justo, ultrices nec erat in, euismod iaculis mauris. Vivamus eleifend vitae nulla vel malesuada. In ac malesuada lacus, et consectetur ante. Fusce vitae lectus sit amet mi pulvinar maximus. Aenean placerat, nibh vel accumsan aliquet, magna nibh accumsan nibh, ac tempus nunc ipsum ac tellus.</div>
  </div>
  <div class="faq" style="top:280px"><div class="faq-head"><svg width="14" height="14" viewBox="0 0 14 14"><circle cx="7" cy="7" r="7" fill="#1159b0"/><text x="7" y="11" font-size="10" text-anchor="middle" fill="#fff" font-family="sans-serif" font-weight="700">?</text></svg>Pellentesque convallis molestie enim sit amet?<svg class="chev" width="12" height="8" viewBox="0 0 12 8"><path d="M1 7 L6 2 L11 7" fill="none" stroke="#1159b0" stroke-width="2"/></svg></div></div>
  <div class="faq" style="top:343px"><div class="faq-head"><svg width="14" height="14" viewBox="0 0 14 14"><circle cx="7" cy="7" r="7" fill="#1159b0"/><text x="7" y="11" font-size="10" text-anchor="middle" fill="#fff" font-family="sans-serif" font-weight="700">?</text></svg>Etiam id imperdiet lectus?<svg class="chev" width="12" height="8" viewBox="0 0 12 8"><path d="M1 7 L6 2 L11 7" fill="none" stroke="#1159b0" stroke-width="2"/></svg></div></div>
  <div class="faq" style="top:407px"><div class="faq-head"><svg width="14" height="14" viewBox="0 0 14 14"><circle cx="7" cy="7" r="7" fill="#1159b0"/><text x="7" y="11" font-size="10" text-anchor="middle" fill="#fff" font-family="sans-serif" font-weight="700">?</text></svg>Cras sollicitudin cursus dui eu placerat?<svg class="chev" width="12" height="8" viewBox="0 0 12 8"><path d="M1 7 L6 2 L11 7" fill="none" stroke="#1159b0" stroke-width="2"/></svg></div></div>
</section>

<section class="video">
  <div class="video-photo" role="img" aria-label="Brick house under renovation with new timber deck frame and ladder"></div>
  <div class="video-tint"></div>
  <svg class="play" width="48" height="48" viewBox="0 0 48 48"><circle cx="24" cy="24" r="22" fill="none" stroke="#fff" stroke-width="3"/><circle cx="24" cy="24" r="19" fill="#fff"/><polygon points="19,14 34,24 19,34" fill="#1b2b44"/></svg>
  <h3>Phasellus congue dapibus sapien.</h3>
</section>

<section class="contact">
  <h2 class="section-title">Contact Us</h2>
  <div class="field" style="left:144px">Full Name</div>
  <div class="field" style="left:375px">Phone</div>
  <div class="field" style="left:607px">Email</div>
  <div class="field" style="left:838px">Choose a Service<svg width="10" height="6" viewBox="0 0 10 6"><polygon points="0,0 10,0 5,6" fill="#555"/></svg></div>
  <div class="message">Message</div>
  <div class="submit btn">SUBMIT</div>
</section>

<footer class="site-footer">
  <svg class="footer-shape" width="1200" height="241" viewBox="0 0 1200 241"><polygon points="0,0 0,241 1200,241 1200,40" fill="#1159b0"/><polygon points="0,76 600,50 1200,40 1200,241 0,241" fill="#0f2540"/><polygon points="0,0 700,68 0,76" fill="#1159b0"/></svg>
  <div class="live-chat">LIVE<br>CHAT</div>
  <div class="footer-links">Home<span>|</span>Our Services<span>|</span>Our Works<span>|</span>About Us<span>|</span>Team<span>|</span>Contact Us</div>
  <div class="copyright">Copyright © 2020 Brackwell Builders. All rights reserved.</div>
  <div class="social"><i></i><i></i><i></i></div>
</footer>

</body>
</html>
```